Business card for a new innovative and professional lawn care business

We need a business card design for a new lawn care business in Halifax NS Canada. We offer lawn services in Halifax & Bedford. Our services offered include lawn care, garden services, and property maintenance. We take pride in our work and are experienced at what we do. I would like to see a design that is double sided. On the backside I would like the something simple (maybe my logo preferably on blackround (linked below) with website link, Facebook page or something). The front I want to include contact info:
Morgan Pell
phone 902-555-0148
email - brookvaleyards.ca
facebook - Facebook.com/brookvaleyards
Instagram maybe ? - instagram.com/brookvaleyard
Serving Halifax and Bedford for 5 years?
I don't want it to have too much information as I will be passing them out in aim to visit website, or call !
We do want it to include lawn care, garden services and property maintenance.
Basic, catchy, and modern looking !
Logo attached below !

Target Market(s)

Passing business cards to everyone I meet or interact with.

Industry/Entity Type

Lawn Care

Contact Information for Business Card

Double sided with some basic information, with catchy colours and easy to look at.

Font styles to use
Sans Serif

Requirements
Must have
• Must be double sided and have :
• Name, Phone, Email, FB, Website, and 3 main services offered - lawn care, property maintenance, garden services
Nice to have
• Would be nice to have instagram link if it goes well on there
Should not have
• Don't want too much writing or images that are distracting

```html
<!DOCTYPE html>
<html lang="en">
<head>
<meta charset="utf-8">
<title>Brookvale Yards – Business Card</title>
<link rel="stylesheet" href="https://fonts.googleapis.com/css2?family=Lato:wght@400;700;900&display=swap">
<style>
  :root{
    --page:#2b2b2b;
    --lime:#7cb82f;
    --forest:#0d6b2c;
    --ink:#2a2a2a;
    --paper:#ffffff;
    --paper-shade:#ececec;
    --charcoal:#3a3a3a;
    --charcoal-dark:#1f1f1f;
    --web-text:#e2f1cc;
  }
  *{box-sizing:border-box;margin:0;padding:0}
  html,body{width:1200px;height:873px;overflow:hidden}
  body{
    background:var(--page);
    font-family:"Lato",sans-serif;
    display:flex;align-items:center;justify-content:center;gap:40px;
  }
  .card{position:relative;width:560px;height:320px;border-radius:18px;overflow:hidden}

  /* Back side */
  .card-back{display:flex;align-items:center;justify-content:center}
  .card-back .facets{
    position:absolute;inset:0;
    background:linear-gradient(135deg,var(--charcoal) 0%,var(--charcoal-dark) 45%,var(--charcoal) 70%,var(--charcoal-dark) 100%);
  }
  .brand-name{position:relative;font-weight:900;color:var(--lime);letter-spacing:.02em;text-transform:uppercase}
  .card-back .brand-name{font-size:44px}

  /* Front side */
  .card-front{background:linear-gradient(180deg,var(--paper) 0%,var(--paper-shade) 100%)}
  .card-front .band{position:absolute;inset:0;width:100%;height:100%}
  .holder{position:absolute;top:20px;left:0;right:0;text-align:center;line-height:1.15}
  .holder-name{font-weight:900;font-size:17px;color:var(--lime);text-transform:uppercase}
  .holder-role{font-weight:700;font-size:11px;color:var(--ink)}
  .card-front .brand-name{position:absolute;top:60px;left:0;right:0;text-align:center;font-size:30px;line-height:36px}
  .services{
    position:absolute;top:101px;left:0;right:0;text-align:center;
    font-size:10px;font-weight:700;letter-spacing:.18em;text-transform:uppercase;color:var(--forest);
  }

  .contact{position:absolute;display:flex;align-items:center;gap:10px;font-size:15px;font-weight:700;color:var(--ink);line-height:22px}
  .contact .icon{width:22px;height:22px;flex:none}
  .contact-phone{left:30px;top:204px}
  .contact-email{left:30px;top:240px}
  .contact-social{left:362px;top:160px}
  .contact-handle{left:362px;top:190px}
  .website{
    position:absolute;bottom:16px;left:0;right:0;text-align:center;
    font-size:13px;font-weight:700;letter-spacing:.42em;color:var(--web-text);
  }
</style>
</head>
<body>

<section class="card card-back" aria-label="Card back">
  <div class="facets" role="img" aria-label="Dark charcoal faceted polygon texture"></div>
  <span class="brand-name">Brookvale Yards</span>
</section>

<section class="card card-front" aria-label="Card front">
  <svg class="band" viewBox="0 0 560 320" preserveAspectRatio="none" aria-hidden="true">
    <path d="M0 167 Q280 132 560 122 L560 320 L0 320Z" fill="var(--forest)"/>
    <path d="M0 175 Q280 140 560 130 L560 320 L0 320Z" fill="var(--lime)"/>
  </svg>

  <div class="holder">
    <div class="holder-name">Morgan Pell</div>
    <div class="holder-role">Owner / Founder</div>
  </div>

  <span class="brand-name">Brookvale Yards</span>
  <div class="services">Lawn Care · Garden Services · Property Maintenance</div>

  <div class="contact contact-phone">
    <svg class="icon" viewBox="0 0 24 24"><circle cx="12" cy="12" r="11" fill="#fff"/><path d="M8.5 6.5l2 2-1.2 1.6a7 7 0 0 0 4.6 4.6l1.6-1.2 2 2-1.4 1.8c-4.6-.2-9.1-4.7-9.3-9.3z" fill="var(--lime)"/></svg>
    <span>902-555-0148</span>
  </div>
  <div class="contact contact-email">
    <svg class="icon" viewBox="0 0 24 24"><circle cx="12" cy="12" r="11" fill="#fff"/><rect x="6" y="8" width="12" height="8.5" rx="1" fill="none" stroke="var(--lime)" stroke-width="1.6"/><path d="M6.5 8.5l5.5 4.3 5.5-4.3" fill="none" stroke="var(--lime)" stroke-width="1.6"/></svg>
    <span>me@brookvaleyards.ca</span>
  </div>
  <div class="contact contact-social">
    <svg class="icon" viewBox="0 0 24 24"><circle cx="12" cy="12" r="11" fill="#fff"/><circle cx="8" cy="12" r="2" fill="var(--lime)"/><circle cx="16" cy="8" r="2" fill="var(--lime)"/><circle cx="16" cy="16" r="2" fill="var(--lime)"/><path d="M8 12L16 8M8 12l8 4" stroke="var(--lime)" stroke-width="1.4"/></svg>
    <span>/brookvaleyards</span>
  </div>
  <div class="contact contact-handle">
    <svg class="icon" viewBox="0 0 24 24"><circle cx="12" cy="12" r="11" fill="#fff"/><path d="M6.5 7.5h11v7h-6l-3 2.5v-2.5h-2z" fill="var(--lime)"/></svg>
    <span>brookvaleyard</span>
  </div>

  <div class="website">www.brookvaleyards.ca</div>
</section>

</body>
</html>
```